Exciting & Elegant Stationary Pack

Stationary consists of
1. Letter head / Envelope
2. Business Card
3. Invoice
4. 40x40mm sticker

Attached files;

1. Logo (Other formats available on request)
2. MS word Doc - For information and description of design
3. Website image (This will be our new website so use the colours so everything ties together)
4. Sample of stationary pack we like, but feel free to be creative

Target Market(s)

Home improvement

Industry/Entity Type

Construction

Font styles to use
Other font styles liked:
• Leave up to designer - We like font used on (website attached image)

Requirements
Must have
• Please look at uploaded file of sample website and use colours
Nice to have
• Any type of business card design - eg. metal, die cut, embossed, etc...

```html
<!DOCTYPE html>
<html lang="en">
<head>
<meta charset="utf-8">
<title>Tilecrest – Business Card</title>
<link href="https://fonts.googleapis.com/css2?family=Oswald:wght@400;600&family=Source+Sans+3:wght@400;700&display=swap" rel="stylesheet">
<style>
  :root {
    --backdrop: #6f6f6f;
    --navy: #133d63;
    --red: #cc2229;
    --sky: #a9cce9;
    --white: #ffffff;
    --ink: #1b1b1b;
    --heading: #26435f;
    --social-a: #2f5e9e;
    --social-b: #d9503f;
    --social-c: #333333;
  }
  * { margin: 0; padding: 0; box-sizing: border-box; }
  html, body { width: 1200px; height: 1149px; overflow: hidden; }
  body { background: var(--backdrop); position: relative; font-family: "Source Sans 3", sans-serif; }

  .card { position: absolute; overflow: hidden; }
  .card--front { left: 114px; top: 160px; width: 704px; height: 402px; background: var(--white); }
  .card--back { left: 370px; top: 632px; width: 706px; height: 400px; background: var(--navy); }
  .card svg.card__art { position: absolute; inset: 0; }

  .brand-name {
    position: absolute; font-family: "Oswald", sans-serif; font-weight: 600;
    letter-spacing: 2px; line-height: 1; white-space: nowrap;
  }
  .card--front .brand-name { left: 40px; top: 60px; font-size: 54px; color: var(--navy); }
  .card--back .brand-name { left: 420px; top: 250px; font-size: 50px; color: var(--white); }

  .connect { position: absolute; right: 46px; top: 54px; text-align: center; }
  .connect__title { font-family: "Oswald", sans-serif; font-weight: 400; font-size: 28px; color: var(--heading); line-height: 1; }
  .connect__icons { display: flex; gap: 20px; margin-top: 14px; justify-content: center; }
  .social-dot { width: 44px; height: 44px; border-radius: 50%; }
  .social-dot--a { background: var(--social-a); }
  .social-dot--b { background: var(--social-b); }
  .social-dot--c { background: var(--social-c); }

  .person { position: absolute; right: 44px; top: 191px; text-align: right; color: var(--white); }
  .person__name { font-weight: 700; font-size: 22px; line-height: 1.1; }
  .person__role { font-size: 16px; line-height: 1.3; }

  .contact { position: absolute; right: 44px; top: 272px; list-style: none; text-align: right; color: var(--ink); font-size: 18px; }
  .contact li { height: 28px; display: flex; justify-content: flex-end; align-items: center; gap: 10px; }
  .contact .contact__icon { width: 16px; height: 16px; flex: none; }
  .contact .contact__plain { padding-right: 26px; }
</style>
</head>
<body>

<section class="card card--front" aria-label="Business card front">
  <svg class="card__art" width="704" height="402" viewBox="0 0 704 402">
    <rect class="band-red" x="0" y="182" width="704" height="73" fill="var(--red)"/>
    <rect class="band-sky" x="0" y="255" width="704" height="147" fill="var(--sky)"/>
    <line x1="0" y1="255" x2="704" y2="255" stroke="var(--white)" stroke-width="3"/>
  </svg>

  <div class="brand-name">TILECREST</div>

  <div class="connect">
    <div class="connect__title">Connect with us</div>
    <div class="connect__icons">
      <span class="social-dot social-dot--a"></span>
      <span class="social-dot social-dot--b"></span>
      <span class="social-dot social-dot--c"></span>
    </div>
  </div>

  <div class="person">
    <div class="person__name">Mara Ellison</div>
    <div class="person__role">Project Manager</div>
  </div>

  <ul class="contact">
    <li><span class="contact__plain">Lic No., 204519k</span></li>
    <li>0400 555 132
      <svg class="contact__icon" viewBox="0 0 16 16"><rect x="4" y="1" width="8" height="14" rx="1.5" fill="none" stroke="var(--ink)" stroke-width="1.6"/><rect x="7" y="12" width="2" height="1.2" fill="var(--ink)"/></svg>
    </li>
    <li>hello@tilecrest.example
      <svg class="contact__icon" viewBox="0 0 16 16"><rect x="1" y="4" width="14" height="9" fill="var(--ink)"/><polyline points="1,4 8,9.5 15,4" fill="none" stroke="var(--sky)" stroke-width="1.2"/></svg>
    </li>
    <li>www.tilecrest.example
      <svg class="contact__icon" viewBox="0 0 16 16"><circle cx="8" cy="8" r="7" fill="var(--ink)"/><ellipse cx="8" cy="8" rx="3" ry="7" fill="none" stroke="var(--sky)" stroke-width="1"/><line x1="1" y1="8" x2="15" y2="8" stroke="var(--sky)" stroke-width="1"/></svg>
    </li>
  </ul>
</section>

<section class="card card--back" aria-label="Business card back">
  <svg class="card__art" width="706" height="400" viewBox="0 0 706 400">
    <rect class="tile-field" width="706" height="400" fill="var(--navy)" role="img" aria-label="Navy brick-bond wall tile pattern"/>
  </svg>
  <div class="brand-name">TILECREST</div>
</section>

</body>
</html>
```